Classy, Elegant, Simple Business Card Design

Looking to have a classy, simple, and elegant design. Want a top notch designed business card. I really like the look of the new torvane credit card. I also like the design I attached. I am trying to reach 21-29 year old females for booking us for there wedding or event. We offer Disc Jockey Service, Photo Booth Rentals, and Uplighting .

Target Market(s)

21-28 year old females

Contact Information for Business Card

Has to have logo, website, email, and phone number

Font styles to use
Other font styles liked:
• open to font choice, modern, clean
Designer to choose
33a6d7
0791cd
0555a3
ffffff

Requirements
Must have
• Has to have logo, website, email, and phone number
Nice to have
• I really like the design of the new torvane credit card. I also included my logo and some designs I like
Should not have
• clutter or too much info

```html
<!DOCTYPE html>
<html lang="en">
<head>
<meta charset="utf-8">
<title>Tidecrest Event Group – Business Card</title>
<link rel="stylesheet" href="https://fonts.googleapis.com/css2?family=Poppins:wght@400;500&display=swap">
<style>
  :root {
    --bg: #1c1c1c;
    --card: #ffffff;
    --blue-light: #33a6d7;
    --blue: #0791cd;
    --blue-deep: #0555a3;
    --text-grey: #555a60;
    --muted: #8a8f94;
    --rule: #9aa0a6;
  }
  html, body {
    margin: 0;
    width: 1200px;
    height: 1200px;
    overflow: hidden;
    background: var(--bg);
    font-family: "Poppins", sans-serif;
  }
  .card {
    position: absolute;
    left: 262px;
    width: 686px;
    height: 392px;
    background: var(--card);
    overflow: hidden;
  }
  .card-front { top: 165px; }
  .card-back { top: 653px; }

  .identity {
    position: absolute;
    right: 389px;
    top: 170px;
    text-align: right;
  }
  .identity .name {
    margin: 0;
    font-size: 22px;
    font-weight: 500;
    color: var(--blue);
    line-height: 1.2;
  }
  .identity .role {
    margin: 0;
    font-size: 15px;
    color: var(--muted);
    line-height: 1.3;
  }
  .divider {
    position: absolute;
    left: 315px;
    top: 165px;
    width: 1px;
    height: 61px;
    background: var(--rule);
  }
  .contacts {
    position: absolute;
    left: 334px;
    top: 164px;
    margin: 0;
    padding: 0;
    list-style: none;
  }
  .contacts li {
    display: flex;
    align-items: center;
    gap: 8px;
    font-size: 16px;
    color: var(--text-grey);
    line-height: 19.5px;
  }
  .contacts svg { width: 12px; height: 12px; flex: none; }

  .services-band {
    position: absolute;
    left: 0;
    top: 327px;
    width: 100%;
    height: 29px;
    background: linear-gradient(90deg, var(--blue), var(--blue-light));
    color: #fff;
    font-size: 16px;
    line-height: 29px;
    text-align: center;
  }

  .brand {
    position: absolute;
    left: 0;
    right: 0;
    top: 168px;
    text-align: center;
  }
  .brand-mark {
    display: block;
    margin: 0 auto 14px;
    width: 18px;
    height: 18px;
    border-radius: 50%;
    background: var(--blue-deep);
  }
  .brand-name {
    margin: 0;
    font-size: 34px;
    font-weight: 500;
    color: var(--blue-deep);
    letter-spacing: 1px;
  }
</style>
</head>
<body>
  <section class="card card-front">
    <div class="identity">
      <p class="name">Daniel Hartley</p>
      <p class="role">President</p>
    </div>
    <div class="divider"></div>
    <ul class="contacts">
      <li>
        <svg viewBox="0 0 12 12"><path d="M2.5 1 L4.5 1 L5.2 3.6 L4 4.6 C4.6 6 5.9 7.4 7.4 8 L8.4 6.8 L11 7.5 L11 9.5 C11 10.3 10.3 11 9.5 11 C5 11 1 7 1 2.5 C1 1.7 1.7 1 2.5 1 Z" fill="var(--blue)"/></svg>
        555-014-2730
      </li>
      <li>
        <svg viewBox="0 0 12 12"><rect x="0.5" y="2.5" width="11" height="7" fill="var(--blue)"/><path d="M0.5 2.5 L6 6.5 L11.5 2.5" fill="none" stroke="#fff" stroke-width="1"/></svg>
        info@tidecrestevents.com
      </li>
      <li>
        <svg viewBox="0 0 12 12"><circle cx="6" cy="6" r="5.5" fill="var(--blue)"/><path d="M3 4 C4.5 3 5 5 6.5 4.5 C7 6 5 7 5.5 9" fill="none" stroke="#fff" stroke-width="1"/></svg>
        www.tidecrestevents.com
      </li>
    </ul>
    <div class="services-band">Disc Jockey Service • Photo Booth Rentals • Uplighting .</div>
  </section>

  <section class="card card-back">
    <div class="brand">
      <span class="brand-mark"></span>
      <p class="brand-name">Tidecrest Event Group</p>
    </div>
  </section>
</body>
</html>
```